Etiketten für Bio Seifen
Zielgruppe
Wir stellen hochwertig 'handgemachte' Bio-Seifen her. Die Zielgruppe ist von 3-99 Jahren und zusätzlich haben wir auch noch Seife für Hunde.
Der Firmenname ist 'Verdolina'
Aufgabenstellung
Das Etikett soll Bezug auf Natur, Bio, Nachhaltigkeit nehmen. Wir stellen uns 'weiche' Aquarellfarben vor...Seife: Lavendel, Calendular, 7 Kräuter etc.
Das Etikett soll auf eine Beutelschachtel. Die Schachtel hat eine Anmaße: Breite 55mm; Höhe 120mm; Tiefe 30mm
Das Etikett soll im vorderen- und hinteren Bereich zusammenhängend geklebt werden.
Das Etikett soll eine Abmaße von: Breite 51mm; Höhe 114mm haben (Vorderseite) Rückseite gleich.
Wir möchten die Produkte auch gerne nummerieren, d.h. jede Seife hat eine Nummer die nicht zu groß dargestellt werden soll aber trotzdem gut leserlich.
Wir haben noch ein paar Bilder hochgeladen wie wir uns das ungefähr vorstellen.

```html
<!DOCTYPE html>
<html lang="de">
<head>
<meta charset="utf-8">
<title>Verdolina – Handgemachte Lavendel Seife</title>
<link rel="stylesheet" href="https://fonts.googleapis.com/css2?family=Open+Sans:wght@400&family=Oranienbaum&display=swap">
<style>
  :root {
    --ink: #3a4350;
    --paper: #ffffff;
    --wash-deep: #a9c6e3;
    --wash-mid: #c9dcef;
    --wash-light: #eef4fa;
    --sprig-tone: #c9cdd3;
  }
  * { margin: 0; padding: 0; box-sizing: border-box; }
  html, body { width: 1200px; height: 537px; overflow: hidden; background: var(--paper); }
  .label {
    position: relative;
    width: 1200px;
    height: 537px;
    overflow: hidden;
  }
  .watercolor-backdrop {
    position: absolute;
    inset: 0;
    background:
      radial-gradient(ellipse 420px 260px at 120px 90px, var(--wash-deep) 0%, transparent 75%),
      radial-gradient(ellipse 380px 240px at 1080px 120px, var(--wash-mid) 0%, transparent 75%),
      radial-gradient(ellipse 500px 200px at 900px 440px, var(--wash-mid) 0%, transparent 80%),
      radial-gradient(ellipse 460px 220px at 250px 470px, var(--wash-light) 0%, transparent 80%),
      linear-gradient(180deg, var(--wash-mid) 0%, var(--wash-light) 70%, #f7fafd 100%);
  }
  .seal {
    position: absolute;
    left: 0; top: 0;
    width: 1200px; height: 537px;
  }
  .seal-sprigs {
    position: absolute;
    left: 475px; top: 112px;
    width: 250px; height: 84px;
    border-radius: 50%;
    background: radial-gradient(ellipse at center, var(--sprig-tone) 0%, rgba(201,205,211,0.4) 55%, rgba(255,255,255,0) 100%);
  }
  .seal-text {
    position: absolute;
    left: 0; width: 1200px;
    text-align: center;
    color: var(--ink);
    line-height: 1;
    font-weight: 400;
  }
  .tagline {
    top: 223px;
    font-family: "Open Sans", sans-serif;
    font-size: 23px;
  }
  .product-name {
    top: 259px;
    font-family: "Oranienbaum", serif;
    font-size: 54px;
    letter-spacing: 0;
  }
  .name-dot {
    position: absolute;
    top: 282px;
    width: 9px; height: 9px;
    border-radius: 50%;
    background: var(--ink);
  }
  .name-dot--left { left: 402px; }
  .name-dot--right { left: 789px; }
  .maker {
    top: 337px;
    font-family: "Oranienbaum", serif;
    font-size: 23px;
    letter-spacing: 0.5px;
  }
  .batch-number {
    top: 450px;
    font-family: "Oranienbaum", serif;
    font-size: 22px;
  }
</style>
</head>
<body>
<main class="label">
  <div class="watercolor-backdrop" role="img" aria-label="Weiche blaue Aquarellfläche mit großen, blassen Lavendelzweigen"></div>

  <svg class="seal" viewBox="0 0 1200 537" aria-hidden="true">
    <circle cx="600" cy="272" r="231" fill="var(--paper)" stroke="var(--ink)" stroke-width="6"/>
    <circle cx="600" cy="272" r="221" fill="none" stroke="var(--ink)" stroke-width="2"/>
  </svg>

  <div class="seal-sprigs" role="img" aria-label="Zwei gezeichnete Lavendelzweige"></div>

  <p class="seal-text tagline">Handgemachte</p>
  <span class="name-dot name-dot--left" aria-hidden="true"></span>
  <h1 class="seal-text product-name">LAVENDEL SEIFE</h1>
  <span class="name-dot name-dot--right" aria-hidden="true"></span>
  <p class="seal-text maker">VERDOLINA 2022</p>
  <p class="seal-text batch-number">No. 1</p>
</main>
</body>
</html>
```